A new website is needed for a breakthrough creative thinking tool

My name is Rob Telford - i have a PhD in Organisational Creativity and have written a few books on creative & speed thinking. You can check me out by visiting www.drrobtelford.example

I have uncovered an amazing insight of what stops most people from being more creative.

Themselves.

They filter & judge their own rich, new ideas. I have found the best way to overcome this self-limiting behaviour is to encourage people to think of ideas really quickly so they have no time to judge - they just create.

I call this accelerated form of creativity - Speed Thinking and the tool i have developed is Notion Sprint. There are 5 steps - Start, enhance, connect, evaluate & action.

The most important step is the start where i ask each person to create 9 ideas in 2 minutes using a visual bubble format (see the uploaded file). For many people this magic formula (my wording) is the very essence of an Notion Sprint.

I have also developed a new mobile app (iphone & ipad) which you can find here -

http://lnk.example/7QpR2mX

I wish to develop a new word press site which promotes Notion Sprint.

My vision is to have all the world Blitzing. In a time-poor world where students, managers, leaders & small business owners are being asked to be more creative, innovative and do more with less - we need better, faster tools.

Notion Sprint is an ideal tool for this new world.

I passionately believe in the power of Notion Sprint to unlock amazing creativity in the most logical of people.

I have tested this new tool with thousands of people across Australia, Asia and the US.

I would like to develop a web site which is as creative as the tool itself. My aim is top create a site that explains the concept of an Notion Sprint through the use of videos, blogs and refer visitors to the new mobile app.

I would like this site to be talked about and help to create a movement of Blitzers around the world.

Notion Sprint is the next great creative thinking tool after Brainstorming (developed 70 years ago) & Mindmapping (developed 30 years ago).

Notion Sprint can be used by an individual, partner or group.

The key benefits of using an Notion Sprint are:
- It is a simple, practical, effective way of unlocking the creativity of everyone.
- Notion Sprint is fast & time efficient.
- It helps people who procrastinate to get started (some 20-25% of the adult population are chronic procrastinators; 70% plus for students).
- It enables everyone in group work to contribute their ideas because each person has to create 9 ideas in 2 minutes
- People feel more confident and energised and
- It accelerates progress
Updates

this brief is for a design only

someone else will build the word press site
thanks rob

Reason: Some of the designs are close but require some more work as per my feedback. thanks rob

As part of my requirements i would also like to see 2-3 website pages other than the homepage.

thanks rob

Target Market(s)

This is a mass market product.

But it is a new concept.

Think how Cerebrant is trying to position and sell their brain training games.

Any student, manager, leader or small business owner can use this tool/app.

In large organisations it would engage and interest anyone involved in marketing, innovation, advertising, research, HR, new product development, customer service, training, sales etc.

The people who are most interested in my work have a particular mindset - they are open to new ideas, want to challenge the status quo, welcome change, like learning, sharing and collaborating.

The other segment are those people who are interested in helping others to reach their potential e.g. teachers, trainers, facilitators, coaches etc.

Industry/Entity Type

Small Business

Requirements
Must have
• The Notion Sprint web site design should be clean, simple and answer the following questions:

- What is an Notion Sprint? A breakthrough thinking tool and app that overcomes the biggest barrier that stops most people from being more creative ( or reaching their full creative potential) - i.e. their own internal judging, critical voice.

It's your mobile creative system.

- Who should Blitz? High School right through to university students, small business owners, managers & leaders.

When to Blitz: You can Blitz at any time - in a bus, train, subway, work in the class room. But here are some specific examples
- In a brainstorming, ideation, planning session
- In group work
- You can use as a weekly to do list
- When you need to solve a problem or generate an idea
- You have a flash of inspiration and want to capture an idea or make an existing idea 9 times better
- To do an initial structure an essay, project, assignment, presentation or speech.
- To summarise a topic etc etc etc
Nice to have
• I have an existing web site www.drrobtelford.example

It might be useful to have a potential visual link with this site but this is a nice to have.

The bubbles (see the uploaded file) are an important part of the Notion Sprint tool so this might be worth highlighting in some way (the bubbles help users to make connections and escape thinking in a logical, structured, list type way).

```html
<!DOCTYPE html>
<html lang="en">
<head>
<meta charset="utf-8">
<title>Notion Sprint – Support</title>
<link href="https://fonts.googleapis.com/css2?family=PT+Sans:wght@400;700&family=PT+Sans+Narrow:wght@400;700&display=swap" rel="stylesheet">
<style>
:root{
  --header-top:#3d4d52;
  --header-bottom:#25353a;
  --hero-deep:#0b4a5c;
  --hero-mid:#15728a;
  --hero-glow:#36c6e0;
  --accent:#1f9fd6;
  --accent-dark:#136e9a;
  --link-blue:#0f5f86;
  --text:#444;
  --muted:#777;
  --band:#f0f0f0;
  --border:#cfcfcf;
  --join-red:#b8403a;
  --footer:#2e2e2e;
  --footer-text:#b5b5b5;
  --white:#fff;
}
*{box-sizing:border-box;margin:0;padding:0}
html,body{width:958px;height:1200px;overflow:hidden}
body{font-family:"PT Sans",sans-serif;color:var(--text);background:var(--white);position:relative}
.abs{position:absolute}

/* header */
.site-header{position:absolute;left:0;top:0;width:958px;height:108px;background:linear-gradient(var(--header-top),var(--header-bottom));border-bottom:1px solid #1a2528}
.brand{left:82px;top:22px;display:flex;align-items:center;gap:10px}
.brand-dot{width:52px;height:52px;border-radius:50%;background:var(--hero-glow)}
.brand-name{font-weight:700;font-size:30px;color:var(--white);letter-spacing:.5px;margin-top:26px}
.top-contact{right:80px;top:24px;font-size:12.5px;color:#dfe6e8}
.top-contact span.sep{color:#8a9a9e;margin:0 10px}
.main-nav{right:75px;top:67px;display:flex;gap:25px;align-items:center;font-size:12px;color:var(--white)}
.main-nav .active{background:var(--accent);border:1px solid #6fc6ef;border-radius:3px;padding:3px 7px}

/* hero */
.hero{left:0;top:108px;width:958px;height:342px;background:radial-gradient(circle at 70% 40%,var(--hero-mid),var(--hero-deep) 75%)}
.hero-title{left:130px;top:45px;font-size:43px;font-weight:400;color:#7fd6ee;letter-spacing:-.5px}
.hero-sub{left:130px;top:108px;font-size:20px;line-height:25px;color:var(--white)}
.btn-download{left:130px;top:179px;width:145px;height:37px;background:#ececec;border:1px solid #bbb;border-radius:2px;font-size:18px;color:#333;display:flex;align-items:center;justify-content:center}
.btn-store{left:286px;top:179px;width:113px;height:37px;background:#111;border:1px solid #666;border-radius:4px;color:var(--white);display:flex;flex-direction:column;justify-content:center;padding-left:28px}
.btn-store small{font-size:8.5px;line-height:10px}
.btn-store b{font-size:16px;font-weight:400;line-height:17px}
.btn-store i{position:absolute;left:9px;top:9px;width:11px;height:19px;border:2px solid var(--white);border-radius:2px}
.hero-art{left:541px;top:13px;width:284px;height:284px;border-radius:50%;background:radial-gradient(circle,#5fe3f3 0%,#1fa5c0 45%,rgba(21,114,138,0) 72%)}
.slider-dots{left:106px;top:308px;display:flex;gap:8px}
.slider-dots i{width:11px;height:11px;border-radius:50%;background:#7d9aa3;border:1px solid #4b6770}
.slider-dots i.on{background:#2f4e57}

/* support */
.section-title{font-size:27px;color:var(--accent);font-weight:400}
.support-title{left:96px;top:470px}
.form-intro{left:96px;top:527px;font-size:17px;color:var(--muted)}
.field-label{left:96px;font-size:12px;color:#555}
.field{left:246px;width:204px;height:26px;border:1px solid var(--border);background:var(--white)}
.field.tall{height:73px}
.btn-submit{left:465px;top:721px;width:61px;height:30px;background:linear-gradient(#3db3ea,var(--accent));border:1px solid var(--accent-dark);border-radius:3px;color:var(--white);font-size:15px;display:flex;align-items:center;justify-content:center}
.divider{left:571px;top:529px;width:1px;height:223px;background:#ddd}
.contact-icon{left:610px;top:527px;width:21px;height:21px;border-radius:3px;background:#e2e2e2}
.contact-title{left:642px;top:526px;font-size:16.5px;color:#555}
.contact-line{left:609px;white-space:nowrap}
.c-small{font-size:10.5px;color:#444}
.c-company{font-size:12.5px;color:var(--link-blue)}
.c-link{font-size:13.5px;color:var(--accent)}
.c-plain{font-size:12.5px;color:#444}

/* blog */
.blog-band{left:0;top:786px;width:958px;height:214px;background:var(--band)}
.blog-title{left:87px;top:18px;font-size:21px}
.blog-arrows{left:834px;top:22px;display:flex;gap:8px}
.blog-photo{left:87px;top:55px;width:211px;height:128px;background:linear-gradient(135deg,#2d6147,#1c4a35)}
.post-title{left:312px;top:52px;font-size:14.5px;color:var(--accent-dark)}
.post-text{left:312px;top:81px;width:555px;font-size:11.5px;line-height:20px;color:#555}
.post-bar{left:313px;top:151px;width:546px;height:32px;background:var(--white);border:1px solid #ddd;border-radius:3px;display:flex;align-items:center;font-size:11px;color:#333}
.post-bar .read{width:96px;padding-left:21px;border-right:1px solid #ddd;height:20px;line-height:20px}
.shares{display:flex;gap:8px;padding-left:30px;width:349px;border-right:1px solid #ddd;height:20px;align-items:center}
.pill{font-size:9px;border:1px solid #c8c8c8;border-radius:2px;padding:1px 5px;background:#f4f4f4;color:#333}
.pill.count{background:var(--white)}
.pill.orange{background:#f05a2b;color:var(--white);border-color:#d54a20}
.share-group{display:flex;gap:3px}
.post-bar .date{padding-left:20px}

/* join */
.join-heading{left:0;top:1022px;width:958px;text-align:center;font-family:"PT Sans Narrow",sans-serif;font-size:21px;color:#333}
.join-heading em{font-style:normal;color:var(--join-red);margin-right:6px}
.join-field{top:1066px;height:31px;border:1px solid #d6d6d6;border-radius:2px;background:linear-gradient(#fff 80%,#f1f1f1);font-size:11.5px;color:#777;padding:9px 11px}
.btn-join{left:689px;top:1066px;width:86px;height:31px;background:linear-gradient(#2a9fc3,#177d9e);border:1px solid #0f6580;border-radius:2px;color:var(--white);font-family:"PT Sans Narrow",sans-serif;font-size:16px;display:flex;align-items:center;justify-content:center}

/* footer */
.site-footer{left:0;top:1118px;width:958px;height:82px;background:var(--footer);color:var(--footer-text)}
.footer-nav{left:81px;top:17px;font-size:11px}
.footer-nav .sep{margin:0 7px}
.copyright{left:81px;top:47px;font-size:10.5px}
.social{left:775px;top:30px;display:flex;gap:8px}
.social i{width:20px;height:20px;border-radius:50%;background:#666}
</style>
</head>
<body>

<header class="site-header">
  <div class="abs brand"><span class="brand-dot"></span><span class="brand-name">NOTION SPRINT</span></div>
  <div class="abs top-contact">Phone: 61 2 9010 4471<span class="sep">|</span>E-mail: rob@drrobtelford.example<span class="sep">|</span>Visit:&nbsp; www.drrobtelford.example</div>
  <nav class="abs main-nav">
    <span>Home</span><span>About Sprint</span><span>How it works</span><span>FAQ</span><span class="active">Support</span>
  </nav>
</header>

<section class="abs hero">
  <div class="abs hero-art" role="img" aria-label="Glowing circuit-board brain illustration"></div>
  <h1 class="abs hero-title">Notion Sprint</h1>
  <p class="abs hero-sub">The ultimate creativity &amp;<br>productivity tool for ................ !</p>
  <div class="abs btn-download">Download Now</div>
  <div class="abs btn-store"><i></i><small>Available on the</small><b>App Market</b></div>
  <div class="abs slider-dots"><i class="on"></i><i></i><i></i><i></i></div>
</section>

<h2 class="abs section-title support-title">Support</h2>
<p class="abs form-intro">Kindly post your valuable Suggestions &amp;&nbsp; Query</p>

<label class="abs field-label" style="top:563px">Enter your Name</label>
<div class="abs field" style="top:560px"></div>
<label class="abs field-label" style="top:603px">Enter your Email</label>
<div class="abs field" style="top:601px"></div>
<label class="abs field-label" style="top:643px">Enter your Phone Number</label>
<div class="abs field" style="top:643px"></div>
<label class="abs field-label" style="top:683px">Add Your Comments Here:</label>
<div class="abs field tall" style="top:678px"></div>
<div class="abs btn-submit">Submit</div>

<div class="abs divider"></div>
<div class="abs contact-icon"></div>
<h3 class="abs contact-title">Contact Details</h3>
<p class="abs contact-line c-small" style="top:559px">Dr Rob Telford’s formal company name is:</p>
<p class="abs contact-line c-company" style="top:577px">The Fresh Thinking Company Pty. Ltd</p>
<p class="abs contact-line c-link" style="top:611px">Call me on +61 2 9010 4471</p>
<p class="abs contact-line c-link" style="top:636px">Email: rob@drrobtelford.example</p>
<p class="abs contact-line c-link" style="top:661px">Follow: Drrobtelford</p>
<p class="abs contact-line c-plain" style="top:692px">ABN: 48019273364</p>
<p class="abs contact-line c-plain" style="top:714px">17 Harbour Lane, Bayview, 2104, Sydney, Australia</p>
<p class="abs contact-line c-plain" style="top:736px">Start creating!</p>

<section class="abs blog-band">
  <h2 class="abs section-title blog-title">Blog</h2>
  <div class="abs blog-arrows">
    <svg width="8" height="10" viewBox="0 0 8 10"><path d="M6 1 2 5l4 4" fill="none" stroke="#888" stroke-width="2"/></svg>
    <svg width="8" height="10" viewBox="0 0 8 10"><path d="M2 1l4 4-4 4" fill="none" stroke="#888" stroke-width="2"/></svg>
  </div>
  <div class="abs blog-photo" role="img" aria-label="Chalkboard drawing of light bulbs with a hand holding chalk"></div>
  <h3 class="abs post-title">Curabitur imperdiet luctus justo nec</h3>
  <p class="abs post-text">Morbi dapibus est dui, id tincidunt odio pellentesque ac. Mauris pharetra magna id egestas lacinia. Cras mi nibh, pretium et lobortis ornare, dictum sed elit. Fusce ac vulputate dui. Class aptent taciti sociosqu ad litora torquent per conubia nostra, per inceptos himenaeos. Aenean sed tempor dolor, ut condimentum libero.</p>
  <div class="abs post-bar">
    <span class="read">READ MORE</span>
    <div class="shares">
      <span class="share-group"><span class="pill">Like</span><span class="pill count">3k</span></span>
      <span class="share-group"><span class="pill">Post</span><span class="pill count">316</span></span>
      <span class="share-group"><span class="pill">+1</span><span class="pill count">81</span></span>
      <span class="share-group"><span class="pill orange">Share</span><span class="pill count">4.6K</span></span>
    </div>
    <span class="date">Nov-20-2103</span>
  </div>
</section>

<h2 class="abs join-heading"><em>JOIN THE COMMUNITY</em> FOR MY FREE PAPER BASED NOTION SPRINT TEMPLATES</h2>
<div class="abs join-field" style="left:183px;width:244px">Name</div>
<div class="abs join-field" style="left:437px;width:243px">E-mail</div>
<div class="abs btn-join">JOIN NOW</div>

<footer class="abs site-footer">
  <nav class="abs footer-nav">Home<span class="sep">|</span>About Sprint<span class="sep">|</span>How it works<span class="sep">|</span>FAQ<span class="sep">|</span>Support<span class="sep">|</span>Contact us</nav>
  <p class="abs copyright">Copyright&nbsp; ©&nbsp; 2013&nbsp; Notion Sprint.&nbsp; All rights reserved.</p>
  <div class="abs social"><i></i><i></i><i></i><i></i></div>
</footer>

</body>
</html>
```